Visitenkarten und Briefpapier
Zielgruppe
Planung und Realisierung von individuellen und wertbeständigen Kamin- und Ofenlösungen, sowie Fliesen- und Baddesign.
Aufgabenstellung
Wir benötigen ein möglichst schlichtes Design für Visitenkarten, bzw. Briefpapier. Für die Visitenkarten gerne auch Vorschläge mit Prägung, Ausstanzung oder mit Heißfolie. Auch Klappkarten wären denkbar. Das Design soll "das gewisse Etwas haben" und nicht zu verspielt sein.
Die Visitenkarten sind für die Firma KORVA, das Logo von der Ausstellung "raumfunke" soll dezent mit eingebunden werden (bei dem Briefpapier z.B. in der Fußzeile". Die farbliche Gestaltung sollte sich an den Farben des Logos orientieren.
Schriftart für Texte: Century Gothic
Schriftfarbe: RAL 7016
Nur eine Idee: Ich könnte mir auch gut vorstellen, dass die Visitenkarte aus einer Zündholzverpackung (wenn dann aber eine besondere mit nur einem Zündholz oder einem besonders breiten) besteht: http://glimmvelo.de/produkte_briefchen.php

```html
<!DOCTYPE html>
<html lang="de">
<head>
<meta charset="utf-8">
<title>KORVA – Briefpapier und Visitenkarten</title>
<link href="https://fonts.googleapis.com/css2?family=Didact+Gothic&display=swap" rel="stylesheet">
<style>
  :root {
    --backdrop: #e9e6e2;
    --paper: #ffffff;
    --ink: #3e4347;
    --accent: #f08a24;
    --card-dark: #4b4b4d;
    --rule: #c9c9c9;
    --on-dark: #f2f2f2;
  }
  * { margin: 0; padding: 0; box-sizing: border-box; }
  html, body { width: 1200px; height: 1140px; overflow: hidden; }
  body {
    position: relative;
    background: var(--backdrop);
    font-family: "Didact Gothic", "Century Gothic", sans-serif;
    color: var(--ink);
  }

  /* Letterhead */
  .letterhead {
    position: absolute; left: 42px; top: 40px;
    width: 743px; height: 1050px;
    background: var(--paper);
    box-shadow: 0 2px 8px rgba(0,0,0,.18);
  }
  .letterhead .brand { position: absolute; left: 61px; top: 46px; }
  .brand-name {
    font-size: 38px; line-height: 1; letter-spacing: 1px; color: var(--ink);
  }
  .brand-tagline { font-size: 12.5px; margin-top: 2px; letter-spacing: .2px; }
  .letterhead .contact {
    position: absolute; right: 37px; top: 56px;
    text-align: right; font-size: 12.5px; line-height: 14.5px;
  }
  .contact .digital { color: var(--accent); }
  .rule { position: absolute; left: 36px; right: 37px; height: 1px; background: var(--rule); }
  .rule.header { top: 113px; }
  .rule.footer { top: 1007px; }
  .footer-mark {
    position: absolute; left: 362px; top: 962px;
    width: 16px; height: 16px; border-radius: 50%; background: var(--accent);
  }

  /* Business cards */
  .card {
    position: absolute; left: 808px; width: 357px; height: 199px;
    border-radius: 8px; box-shadow: 0 2px 8px rgba(0,0,0,.2);
  }
  .card-front { top: 40px; background: var(--card-dark); color: var(--on-dark); }
  .card-back { top: 280px; background: var(--paper); }

  .card-front .contact {
    position: absolute; left: 47px; top: 72px; font-size: 9px; line-height: 10px;
  }
  .card-front .contact p + p { margin-top: 10px; }
  .card-front .digital { color: var(--accent); }
  .card-front .brand { position: absolute; left: 224px; top: 94px; }
  .card-front .brand-name { font-size: 26px; color: var(--on-dark); }
  .card-front .brand-tagline { font-size: 8.5px; margin-top: 1px; }
  .card-front .mark {
    position: absolute; left: 168px; top: 90px;
    width: 30px; height: 30px; border-radius: 50%; background: var(--accent);
  }

  .card-back .mark {
    position: absolute; left: 164px; top: 84px;
    width: 32px; height: 32px; border-radius: 50%; background: var(--accent);
  }
  .card-back .person { position: absolute; left: 222px; top: 96px; }
  .person-name { font-size: 14px; line-height: 16px; }
  .person-role { font-size: 9px; color: var(--accent); }
</style>
</head>
<body>

<section class="letterhead" aria-label="Briefpapier">
  <div class="brand">
    <div class="brand-name">KORVA</div>
    <div class="brand-tagline">kamine · öfen · fliesen</div>
  </div>
  <address class="contact" style="font-style:normal">
    <p>Lindenstraße 12, 34212 Feldbrunn</p>
    <p>tel 05674 / 31 48 20 |&nbsp; fax 05674 / 31 48 29</p>
    <p class="digital">info@korva-feldbrunn.de | &nbsp;www.korva-feldbrunn.de</p>
  </address>
  <div class="rule header"></div>
  <div class="footer-mark"></div>
  <div class="rule footer"></div>
</section>

<section class="card card-front" aria-label="Visitenkarte Vorderseite">
  <address class="contact" style="font-style:normal">
    <p>Lindenstraße 12<br>34212 Feldbrunn</p>
    <p>tel 05674 / 31 48 20<br>fax 05674 / 31 48 29</p>
    <p class="digital">info@korva-feldbrunn.de<br>www.korva-feldbrunn.de</p>
  </address>
  <div class="mark"></div>
  <div class="brand">
    <div class="brand-name">KORVA</div>
    <div class="brand-tagline">kamine · öfen · fliesen</div>
  </div>
</section>

<section class="card card-back" aria-label="Visitenkarte Rückseite">
  <div class="mark"></div>
  <div class="person">
    <div class="person-name">Jonas Korva</div>
    <div class="person-role">Geschäftsführer</div>
  </div>
</section>

</body>
</html>
```